One of Australia's fastest growing energy maintenance contractors needs a new website

www.brightleaf.com.au
Our business has evolved over the past years and now our website is no longer relevant.
We clean solar panels and we vacuum roof gutters.
We clean solar panels on the roofs of residential houses right up to billion dollar solar farms with in excess of 1 million panels. We offer thermal image testing and bird proofing for our residential and commercial clients and thermal drone imaging services for our solar farm clients.
We vacuum clean roof gutters (using a LoftSuck) on the residential house next door right up to enormous private and public schools, colleges, shopping centres, strat complexes and commercial buildings.
When first built our business had more of a domestic residential skew and the website reflected that. While that is still part of our core business we are now bidding on and have secured large government, commercial and infrastructure contracts and our new website needs to reflect our growth and our new business. We need a new site that it optimised for both desktop ad phone viewing as our latest figures showed that 73% of people visiting our site are on mobile phones. We have an extensive amount of data on Tallymark Insights available as well as Bidlines. Both that would also need integrating with the site along with a few other plugins such as Quilro Chat IQ, Chatterbox etc along with SEO key words etc. We are also the winner and finalists over multiple years of the small business of the year awards and we like to proudly and prominently display those on our site.
We are looking for a new site with a modern professional feel / theme
There is a definitive break in our business between the solar Panel cleaning clients and the gutter cleaning clients so we would like a home page that begins with a simple choice:
Solar Panel Cleaning – Gutter Cleaning
With a professional full screen background image (we have hundreds to choose from) and along the bottom a small area with rights reserved etc, phone number etc (at some point in the future we will split these into two businesses but for now it’s what we have).
After that selection is made we would like a repeat of that same scenario but the selection is:
If it’s Solar Panel Cleaning
(new background image)
Government – Infrastructure – Commercial – Residential
If it’s Gutter Cleaning
(new background image)
Government – Strata – Commercial – Residential
After making those choices then onto the relevant pages with background images relevant to each sector and a them that suits (on the residential we would like to keep the link to our tallymark reviews) - We will provide copy / text for each relevant page.
Other than that, a menu inclusive of the above and:
Resellers Portal – we will provide a link to this from Quilro CRM)
Customer portal (we will supply a link to this from our booking system)
We also need a page for our Solar Resellers / Partners page but we will give them a link to this, it won’t be listed on the site.
Request a quote page (Again we will provide information from Quilro as this will be linked to the CRM)
Standard contact us page inclusive of phone numbers, address and fields supplied from CRM
Sydney – 02 7391 8056
Southern Highlands – 02 4863 1708
Goulburn – 02 4863 1708
Canberra – 02 6172 4385
Wollongong – 02 4239 5817
sales@brightleaf.com.au
Head Office - Fernbrook NSW 2581
ABN: 48093716552
Responsive Design: Optimized for desktop and mobile (73% mobile visitors).
Fast Loading Speed: Optimized for performance.
Smooth Transition Animations: For service and category selection.
Sticky Contact Bar: Always accessible at the bottom of mobile screens for quick calls.
SEO Optimization: Focused on government tenders, large-scale commercial contracts, and infrastructure projects.
Integrations
Tallymark Insights & Tallymark Bidlines.
Quilro Chat IQ.
Chatterbox Beacon.
SEO tools and keyword optimization.
Many many more images available if needed
Target Market(s)
Residential, commercial, Government

```html
<!DOCTYPE html>
<html lang="en">
<head>
<meta charset="utf-8">
<title>Brightleaf — Solar Panel & Roof Gutter Cleaning</title>
<link href="https://fonts.googleapis.com/css2?family=Lexend+Exa:wght@400;500;600&family=Poppins:wght@400;500;600;700&display=swap" rel="stylesheet">
<style>
:root{
  --blue:#1689d4;
  --blue-dark:#0a63b3;
  --blue-light:#35b0ea;
  --ink:#1f1f1f;
  --muted:#6b6b6b;
  --line:#e3e3e3;
  --footer:#222326;
  --white:#fff;
  --star:#f5b400;
}
*{box-sizing:border-box;margin:0;padding:0}
html,body{width:1200px;height:4556px;overflow:hidden}
body{position:relative;background:var(--white);font-family:'Poppins',sans-serif;color:var(--ink)}
.abs{position:absolute}
.display{font-family:'Lexend Exa',sans-serif;font-weight:500;text-transform:uppercase;letter-spacing:.5px}
.hex{clip-path:polygon(50% 0,100% 25%,100% 75%,50% 100%,0 75%,0 25%)}
.btn{position:absolute;display:flex;align-items:center;justify-content:center;font-size:12px;font-weight:600;text-transform:uppercase;color:#fff;background:linear-gradient(90deg,var(--blue-dark),var(--blue-light));text-decoration:none}
.photo{background:linear-gradient(135deg,#7fa8c9,#3f6f9a 55%,#2a4a6a)}

/* top bar */
.topbar{left:627px;top:0;width:573px;height:36px;background:linear-gradient(90deg,var(--blue-dark),var(--blue-light));clip-path:polygon(4% 0,100% 0,100% 100%,0 100%);display:flex;align-items:center;gap:24px;padding-left:40px;color:#fff;font-size:11.5px;white-space:nowrap}
.topbar span{display:flex;align-items:center;gap:6px}
.brand{left:88px;top:40px;display:flex;align-items:center;gap:10px;font-size:22px;font-weight:600;color:var(--ink)}
.brand i{width:14px;height:14px;background:var(--blue);display:block}
.nav{left:369px;top:66px;display:flex;gap:31px;font-size:13px;color:var(--ink)}
.quote-btn{left:977px;top:53px;width:133px;height:48px;border:2px solid var(--blue);color:var(--blue);font-size:12px;font-weight:600;display:flex;align-items:center;justify-content:center}

/* hero */
.hero-title{left:87px;top:294px;font-size:33px;line-height:39px}
.hero-text{left:88px;top:426px;width:490px;font-size:14px;line-height:22px;color:var(--muted)}
.hero-btn{left:88px;top:486px;width:174px;height:48px}
.hero-backdrop{left:645px;top:150px;width:520px;height:600px;background:linear-gradient(180deg,var(--blue-light),var(--blue-dark))}
.hero-photo{left:670px;top:115px;width:530px;height:609px}
.hero-badge{left:728px;top:592px;width:127px;height:124px;background:#fff;display:flex;align-items:center;justify-content:center;font-size:14px;font-weight:600;color:var(--blue);filter:drop-shadow(0 6px 12px rgba(0,0,0,.15))}
.panel-deco{width:240px;height:165px;background:linear-gradient(135deg,#3a4a5e,#1c2633);transform:skewY(22deg) rotate(-8deg);opacity:.9}

/* services */
.section-title{left:0;width:1200px;text-align:center;font-size:28px}
.tabs{left:330px;top:800px;display:flex;gap:0;font-family:'Lexend Exa',sans-serif;font-size:15px;text-transform:uppercase}
.tabs span{padding:4px 20px 10px}
.tabs .active{border-bottom:2px solid var(--blue)}
.tabs span:last-child{border-bottom:2px solid var(--line)}
.service{width:240px;height:278px;display:flex;flex-direction:column;align-items:center;justify-content:center;gap:14px;text-align:center;font-family:'Lexend Exa',sans-serif;font-size:12.5px;line-height:17px;text-transform:uppercase;background:#fff}
.service-wrap{filter:drop-shadow(0 4px 18px rgba(0,0,0,.09))}
.service-outline{background:var(--blue);width:240px;height:278px}
.service-outline .service{position:absolute;left:2px;top:2px;width:236px;height:274px}

/* about */
.about-backdrop{left:370px;top:1300px;width:200px;height:380px;background:var(--blue);clip-path:polygon(0 0,100% 25%,100% 75%,0 100%)}
.about-photo{left:141px;top:1233px;width:410px;height:476px}
.about-title{left:631px;top:1306px;font-size:27px}
.about-text{left:631px;top:1352px;width:430px;font-size:13.5px;line-height:22px;color:var(--muted)}
.about-text p+p{margin-top:10px}
.about-btn{left:631px;top:1587px;width:138px;height:49px}
.lights-deco{left:900px;top:1617px;width:275px;height:256px;background:linear-gradient(160deg,#e8ecef,#b9c1c8);clip-path:polygon(20% 0,100% 20%,100% 100%,85% 100%,80% 40%,0 35%,0 25%)}

/* portals */
.portal-band{left:0;top:1824px;width:1200px;height:473px;background:linear-gradient(135deg,var(--blue-light),var(--blue-dark));clip-path:polygon(6% 0,94% 0,100% 36%,100% 64%,94% 100%,6% 100%,0 64%,0 36%)}
.portal-title{left:0;top:1888px;width:1200px;text-align:center;color:#fff;font-size:28px}
.portal-text{left:200px;top:1940px;width:800px;text-align:center;color:#fff;font-size:13.5px;line-height:22px}
.portal-card{top:2022px;width:397px;height:351px;display:flex;flex-direction:column;justify-content:flex-end;align-items:center;padding-bottom:30px;color:#fff;background:linear-gradient(180deg,#8a98a6,#4a5866 60%,#2c3640)}
.portal-card h3{font-family:'Lexend Exa',sans-serif;font-weight:500;font-size:18px;text-transform:uppercase}
.portal-card p{font-size:15px;margin-top:6px}

/* quote */
.quote-title{left:145px;top:2580px;font-size:29px;line-height:39px}
.quote-list{left:145px;top:2674px;list-style:none;font-family:'Lexend Exa',sans-serif;font-size:14px;text-transform:uppercase}
.quote-list li{display:flex;align-items:center;gap:10px;height:28.5px}
.contact-cols{left:145px;top:2774px;display:flex;gap:58px;font-size:13px;line-height:21px}
.contact-cols h4{font-family:'Lexend Exa',sans-serif;font-weight:500;font-size:13px;color:var(--blue);text-transform:uppercase;margin-bottom:6px}
.quote-backdrop{left:655px;top:2520px;width:160px;height:340px;background:var(--blue);clip-path:polygon(100% 0,100% 100%,0 75%,0 25%)}
.quote-photo{left:675px;top:2483px;width:380px;height:419px}

/* testimonials */
.review{top:3069px;width:322px;height:214px;background:#fff;box-shadow:0 4px 20px rgba(0,0,0,.08);padding:58px 28px 0}
.review p{font-size:12.5px;line-height:22px;color:var(--muted)}
.review .meta{position:absolute;left:28px;right:22px;bottom:22px;display:flex;justify-content:space-between;font-size:13px;font-weight:600}
.review .stars{color:var(--star);letter-spacing:1px;font-size:12px}
.review .quote-mark{position:absolute;right:60px;top:22px;font-size:90px;line-height:80px;color:#e6eef6;font-family:Georgia,serif}
.avatar{top:3034px;width:78px;height:72px;z-index:2}
.dots{left:571px;top:3322px;display:flex;gap:8px}
.dots i{width:13px;height:13px;border-radius:50%;background:#c9cdd2;display:block}
.dots i.on{background:var(--blue)}

/* faq */
.faq-rule{left:177px;top:3391px;width:958px;height:1px;background:var(--line)}
.faq{left:262px;top:3490px;width:676px}
.faq-row{display:flex;justify-content:space-between;align-items:center;height:53px;border-bottom:1px solid var(--line);padding:0 24px;font-family:'Lexend Exa',sans-serif;font-size:12.5px;text-transform:uppercase}
.faq-row b{color:var(--blue);font-weight:400;font-size:18px}
.faq-open{border-left:3px solid var(--blue);box-shadow:0 4px 16px rgba(0,0,0,.07);padding:18px 24px 18px 21px;margin:6px 0 10px}
.faq-open .q{display:flex;justify-content:space-between;font-family:'Lexend Exa',sans-serif;font-size:12.5px;color:var(--blue);text-transform:uppercase}
.faq-open p{font-size:10.5px;line-height:18px;color:var(--muted);margin-top:10px;width:540px}
.faq-all{left:0;top:3878px;width:1200px;text-align:center;font-size:12.5px;font-weight:600;color:var(--blue);text-decoration:underline}

/* cta */
.cta{left:110px;top:3950px;width:982px;height:215px;background:linear-gradient(135deg,var(--blue-light),var(--blue-dark));clip-path:polygon(5% 0,95% 0,100% 35%,100% 100%,0 100%,0 35%)}
.cta-title{left:190px;top:4016px;color:#fff;font-size:25px}
.cta-text{left:190px;top:4059px;width:600px;color:#fff;font-size:15px;line-height:22px}
.cta-btn{left:871px;top:4034px;width:138px;height:48px;background:#fff;color:var(--ink);font-size:12px;font-weight:600;display:flex;align-items:center;justify-content:center}

/* footer */
.footer{left:0;top:4165px;width:1200px;height:391px;background:var(--footer);color:#fff}
.footer-brand{left:99px;top:4312px;display:flex;align-items:center;gap:14px;font-size:30px;font-weight:600;color:#fff}
.footer-brand i{width:22px;height:22px;background:var(--blue);display:block}
.fcol{top:4236px;font-size:12px;color:#dcdcdc}
.fcol h4{font-family:'Lexend Exa',sans-serif;font-weight:500;font-size:17px;color:#fff;text-transform:uppercase;margin-bottom:18px}
.fcol ul{list-style:none}
.fcol li{height:26.5px}
.fcol li::before{content:"›";color:var(--blue);margin-right:8px}
.finfo{display:flex;gap:10px;margin-bottom:16px;line-height:18px}
.finfo svg{flex:none;margin-top:2px}
.newsletter-input{width:202px;height:37px;background:#fff;color:var(--ink);font-size:10.5px;display:flex;align-items:center;justify-content:space-between;padding:0 14px;margin-top:18px}
.socials{display:flex;gap:14px;margin-top:18px}
.socials i{width:11px;height:11px;border-radius:50%;background:#fff;display:block}
.copyright{left:0;top:4514px;width:1200px;text-align:center;color:#fff;font-size:12px;font-weight:600}
.to-top{left:1127px;top:4465px;width:53px;height:54px;background:var(--blue);display:flex;align-items:center;justify-content:center}
</style>
</head>
<body>

<!-- header -->
<div class="abs topbar">
  <span><svg width="10" height="12" viewBox="0 0 10 12"><path d="M5 0a4 4 0 0 1 4 4c0 3-4 8-4 8S1 7 1 4a4 4 0 0 1 4-4z" fill="#fff"/><circle cx="5" cy="4" r="1.5" fill="#1689d4"/></svg>8/22 Millbrook Close, Fernbrook NSW 2581</span>
  <span><svg width="12" height="9" viewBox="0 0 12 9"><rect width="12" height="9" fill="#fff"/><path d="M0 0l6 5 6-5" stroke="#1689d4" fill="none"/></svg>sales@brightleaf.com.au</span>
</div>
<div class="abs brand"><i></i>Brightleaf</div>
<nav class="abs nav"><span>Home</span><span>About Us</span><span>Solar Cleaning</span><span>Gutter Cleaning</span><span>DustLift</span><span>Contact Us</span></nav>
<div class="abs quote-btn">GET A QUOTE</div>

<!-- hero -->
<h1 class="abs display hero-title">Expert Solar<br>Panel &amp; Roof Gutter<br>Cleaning</h1>
<p class="abs hero-text">Protecting your investment with professional cleaning services for homes, businesses, and large-scale infrastructure projects.</p>
<a class="btn hero-btn">Get a Free Quote</a>
<div class="abs hex hero-backdrop"></div>
<div class="abs hex photo hero-photo" role="img" aria-label="Two technicians in safety harnesses cleaning rooftop solar panels under a blue sky"></div>
<div class="abs hex hero-badge">Brightleaf</div>
<div class="abs panel-deco" style="left:-20px;top:670px" role="img" aria-label="Tilted solar panel"></div>

<!-- services -->
<h2 class="abs display section-title" style="top:745px">Our Services</h2>
<div class="abs tabs"><span class="active">Solar Panel Cleaning</span><span>Gutter Cleaning</span></div>

<div class="abs service-wrap" style="left:224px;top:871px">
  <div class="hex service">
    <svg width="64" height="64" viewBox="0 0 64 64" fill="none" stroke="#1689d4" stroke-width="2"><path d="M6 30L32 8l26 22"/><path d="M12 26v32h40V26"/><rect x="26" y="40" width="12" height="18"/><rect x="16" y="32" width="8" height="8"/><rect x="40" y="32" width="8" height="8"/><path d="M44 14v-6h6v11"/></svg>
    <span>Residential &amp;<br>Commercial<br>Cleaning</span>
  </div>
</div>
<div class="abs hex service-outline" style="left:479px;top:871px">
  <div class="hex service">
    <svg width="64" height="64" viewBox="0 0 64 64" fill="none" stroke="#1689d4" stroke-width="2"><rect x="18" y="4" width="28" height="32" rx="3"/><rect x="23" y="9" width="18" height="16"/><path d="M23 20l6-5 5 4 7-6"/><path d="M26 36v10h12V36"/><path d="M28 46v12h8V46"/><circle cx="32" cy="31" r="2"/></svg>
    <span>Thermal<br>Imaging &amp; Drone<br>Inspections</span>
  </div>
</div>
<div class="abs service-wrap" style="left:735px;top:871px">
  <div class="hex service">
    <svg width="64" height="64" viewBox="0 0 64 64" fill="none" stroke="#1689d4" stroke-width="2"><circle cx="44" cy="18" r="7"/><circle cx="44" cy="18" r="2.5"/><path d="M44 7v4M44 25v4M33 18h4M51 18h4"/><path d="M10 58V44l10-6h20l10 6v14"/><path d="M22 38v20M38 38v20"/><rect x="26" y="44" width="8" height="8"/></svg>
    <span>Bird Proofing<br>&amp; Maintenance</span>
  </div>
</div>

<!-- about -->
<div class="abs about-backdrop"></div>
<div class="abs hex photo about-photo" style="background:linear-gradient(135deg,#c9c2b6,#6f7f8f 50%,#2e4259)" role="img" aria-label="Technician in a hard hat and gloves inspecting solar panels with a tool"></div>
<h2 class="abs display about-title">About Brightleaf</h2>
<div class="abs about-text">
  <p>At Brightleaf, we specialize in professional solar panel and gutter cleaning for residential, commercial, and government infrastructure projects. With years of industry experience, our team ensures that your solar panels operate at peak efficiency and that your gutters remain free from blockages, preventing costly damage.</p>
  <p>With fully insured and WWCC-approved staff, we uphold the highest safety and compliance standards, ensuring peace of mind for all our clients.</p>
</div>
<a class="btn about-btn">Read More</a>
<div class="abs lights-deco" role="img" aria-label="Solar-powered street lights"></div>

<!-- portals -->
<div class="abs portal-band"></div>
<h2 class="abs display portal-title">Customer &amp; Reseller Portals</h2>
<p class="abs portal-text">Our dedicated portals make managing services and partnerships easier than ever. Whether you're a customer looking to track bookings or a reseller seeking exclusive benefits, we've got you covered.</p>
<div class="abs portal-card" style="left:196px" role="img" aria-label="Two workers in hard hats reviewing a tablet at a solar farm"><h3>Customer Portal</h3><p>Manage bookings, reports &amp; more</p></div>
<div class="abs portal-card" style="left:608px;background:linear-gradient(180deg,#b8bec4,#5e656c 60%,#2f3439)" role="img" aria-label="Person holding a solar panel beside a small wind turbine"><h3>Reseller Portal</h3><p>Partner with us for exclusive benefits</p></div>

<!-- quote -->
<h2 class="abs display quote-title">Request a Quote<br>Fast &amp; Obligation-Free</h2>
<ul class="abs quote-list">
  <li><svg width="18" height="20" viewBox="0 0 18 20"><path d="M9 0l9 5v10l-9 5-9-5V5z" fill="#1689d4"/><path d="M5 10l3 3 5-6" stroke="#fff" stroke-width="2" fill="none"/></svg>Residential &amp; Commercial</li>
  <li><svg width="18" height="20" viewBox="0 0 18 20"><path d="M9 0l9 5v10l-9 5-9-5V5z" fill="#1689d4"/><path d="M5 10l3 3 5-6" stroke="#fff" stroke-width="2" fill="none"/></svg>Government &amp; Infrastructure</li>
  <li><svg width="18" height="20" viewBox="0 0 18 20"><path d="M9 0l9 5v10l-9 5-9-5V5z" fill="#1689d4"/><path d="M5 10l3 3 5-6" stroke="#fff" stroke-width="2" fill="none"/></svg>Custom Maintenance Plans</li>
</ul>
<div class="abs contact-cols">
  <div><h4>Call Us:</h4>Sydney: <b>02 7391 8056</b><br>Canberra: <b>02 6172 4385</b></div>
  <div><h4>Email:</h4>sales@brightleaf.com.au</div>
</div>
<div class="abs quote-backdrop"></div>
<div class="abs hex photo quote-photo" style="background:linear-gradient(135deg,#5a7290,#2d4560 50%,#e0a050)" role="img" aria-label="Installer in an orange hard hat drilling a solar panel frame"></div>

<!-- testimonials -->
<h2 class="abs display section-title" style="top:2966px">What Our Clients Say</h2>
<div class="abs review" style="left:90px"><span class="quote-mark">“</span><p>Since we partnered with NorthByte our application has never been faster. We no longer worry about traffic spikes or unexpected downtime.</p><div class="meta"><span>Martin Hale</span><span class="stars">★★★★★</span></div></div>
<div class="abs review" style="left:436px"><span class="quote-mark">“</span><p>Since we partnered with NorthByte our application has never been faster. We no longer worry about traffic spikes or unexpected downtime.</p><div class="meta"><span>Martin Hale</span><span class="stars">★★★★★</span></div></div>
<div class="abs review" style="left:781px"><span class="quote-mark">“</span><p>Since we partnered with NorthByte our application has never been faster. We no longer worry about traffic spikes or unexpected downtime.</p><div class="meta"><span>Martin Hale</span><span class="stars">★★★★★</span></div></div>
<div class="abs hex avatar" style="left:116px;background:linear-gradient(#e7b15b,#c98a2e)" role="img" aria-label="Client portrait"></div>
<div class="abs hex avatar" style="left:462px;background:linear-gradient(#a6a0d8,#6d67b0)" role="img" aria-label="Client portrait"></div>
<div class="abs hex avatar" style="left:807px;background:linear-gradient(#f08a6a,#d4503a)" role="img" aria-label="Client portrait"></div>
<div class="abs dots"><i></i><i class="on"></i><i></i></div>

<!-- faq -->
<div class="abs faq-rule"></div>
<div class="abs panel-deco" style="left:-20px;top:3350px" role="img" aria-label="Tilted solar panel"></div>
<h2 class="abs display section-title" style="top:3445px">FAQ's</h2>
<div class="abs faq">
  <div class="faq-row" style="border-bottom:none">Why do I need to clean my gutters?<b>+</b></div>
  <div class="faq-open"><div class="q">What is VacuLine?<span>–</span></div><p>Vacuum roof gutter cleaning is a method that uses high-powered vacuum systems to remove dirt, leaves, and blockages from gutters efficiently without causing damage to your property.</p></div>
  <div class="faq-row">How often should I clean my gutters?<b>+</b></div>
  <div class="faq-row">Will rain clean my solar panels and gutters?<b>+</b></div>
  <div class="faq-row">Does cleaning my solar panels improve performance?<b>+</b></div>
  <div class="faq-row" style="border-bottom:none">Do you provide reports after cleaning?<b>+</b></div>
</div>
<div class="abs faq-all">VIEW ALL FAQS</div>

<!-- footer -->
<div class="abs footer"></div>
<div class="abs cta"></div>
<h2 class="abs display cta-title">Trusted by Industry Leaders</h2>
<p class="abs cta-text">We work with government agencies, businesses, and property managers to ensure top-quality cleaning and maintenance.</p>
<div class="abs cta-btn">READ MORE</div>

<div class="abs footer-brand"><i></i>Brightleaf</div>
<div class="abs fcol" style="left:438px">
  <h4>Quick Links</h4>
  <ul><li>Home</li><li>About Us</li><li>Solar Cleaning</li><li>Gutter Cleaning</li><li>DustLift</li><li>Contact Us</li></ul>
</div>
<div class="abs fcol" style="left:650px;width:200px">
  <h4>Contact Info</h4>
  <div class="finfo"><svg width="12" height="9" viewBox="0 0 12 9"><rect width="12" height="9" fill="#1689d4"/><path d="M0 0l6 5 6-5" stroke="#fff" fill="none"/></svg><span>Email:<br>sales@brightleaf.com.au</span></div>
  <div class="finfo"><svg width="12" height="12" viewBox="0 0 12 12"><path d="M2 0l3 3-1.5 2a7 7 0 0 0 3.5 3.5L9 7l3 3-2 2C5 12 0 7 0 2z" fill="#1689d4"/></svg><span>Phone:<br>02 4863 1708</span></div>
  <div class="finfo"><svg width="10" height="12" viewBox="0 0 10 12"><path d="M5 0a4 4 0 0 1 4 4c0 3-4 8-4 8S1 7 1 4a4 4 0 0 1 4-4z" fill="#1689d4"/></svg><span>Location:<br>8/22 Millbrook Close, Fernbrook NSW 2581</span></div>
</div>
<div class="abs fcol" style="left:899px">
  <h4>Newsletter</h4>
  <div>Subscribe to our newsletter</div>
  <div class="newsletter-input"><span>Email Address</span><svg width="12" height="11" viewBox="0 0 12 11"><path d="M0 5l12-5-3 11-3-4z" fill="#1689d4"/></svg></div>
  <div class="socials"><i></i><i></i><i></i><i></i></div>
</div>
<div class="abs copyright">© Copyright 2025 Brightleaf | All rights reserved</div>
<div class="abs to-top"><svg width="14" height="20" viewBox="0 0 14 20"><path d="M7 19V2M1 8l6-6 6 6" stroke="#fff" stroke-width="2" fill="none"/></svg></div>

</body>
</html>
```